New Business Card Design Project LORVANTI-Italy

we are LORVANTI-Italy
our company in the market for 3 years we are luxury cosmetic company and its about time for a facelift :)
i will like to have elegant luxurious and unique business card
that will give the person that get it a unique, luxurious and elegant impression
I'm VERY OPEN FOR NEW IDEAS , even duo i add a few files of things that i see on line and i like them

i add my logo as well
my website is LORVANTI.COM
(if you would like to see the main style that we have)

Target Market(s)

adult that have money :)

Industry/Entity Type

Business

Contact Information for Business Card

Name - Dario Lorvanti
Position - CEO and CO Founder
address - 4817 E Halvern
telephone - 555-384-1926
email - dario@lorvanti.com
fax - 555-384-1926
website - LORVANTI.COM

Colors
000000
959595
fbee3e
ffffff

Requirements
Must have
• big logo in GOLD color
• elegant look
• impressive
Nice to have
• not must but maybe classy pattern background
• not must but maybe emblem
• maybe clear plastic business card
Should not have
• colors
• images

```html
<!DOCTYPE html>
<html lang="en">
<head>
<meta charset="utf-8">
<title>LORVANTI Italy — Business Card</title>
<link rel="stylesheet" href="https://fonts.googleapis.com/css2?family=EB+Garamond:wght@500&display=swap">
<style>
  :root {
    --backdrop: #2e3f47;
    --gold-light: #e3c983;
    --gold-mid: #c6a459;
    --gold-deep: #8c6b2c;
    --band: #2b2622;
    --ink: #2a2218;
    --gold-text: #e0b845;
  }
  html, body {
    margin: 0;
    width: 1200px;
    height: 900px;
    overflow: hidden;
    background: var(--backdrop);
  }
  .card {
    position: absolute;
    left: 150px;
    top: 193px;
    width: 900px;
    height: 514px;
    display: flex;
    box-shadow: 0 14px 30px rgba(0, 0, 0, 0.35);
  }
  .card__field {
    position: relative;
    flex: 1;
    background: radial-gradient(ellipse at 35% 25%, var(--gold-light) 0%, var(--gold-mid) 45%, var(--gold-deep) 100%);
  }
  .card__mark {
    position: absolute;
    left: 50%;
    top: 50%;
    transform: translate(-50%, -50%);
    display: flex;
    align-items: center;
    gap: 14px;
  }
  .card__mark-dot {
    width: 22px;
    height: 22px;
    border-radius: 50%;
    background: var(--ink);
  }
  .card__mark-name {
    font-family: "EB Garamond", serif;
    font-weight: 500;
    font-size: 44px;
    letter-spacing: 4px;
    color: var(--ink);
  }
  .card__band {
    position: relative;
    width: 220px;
    background: var(--band);
  }
  .wordmark {
    position: absolute;
    left: 50%;
    top: 50%;
    transform: translate(-50%, -50%) rotate(-90deg);
    font-family: "EB Garamond", serif;
    font-weight: 500;
    color: var(--gold-text);
    white-space: nowrap;
  }
  .wordmark__name {
    font-size: 66px;
    line-height: 1;
    letter-spacing: 1px;
    padding: 0 4px 8px;
    border-bottom: 3px solid var(--gold-text);
  }
  .wordmark__country {
    font-size: 20px;
    letter-spacing: 1px;
    text-align: right;
    margin-top: 10px;
    padding-right: 14px;
  }
</style>
</head>
<body>
  <div class="card">
    <div class="card__field" role="img" aria-label="Gold background with a fine geometric diamond pattern">
      <div class="card__mark">
        <span class="card__mark-dot"></span>
        <span class="card__mark-name">LORVANTI</span>
      </div>
    </div>
    <div class="card__band">
      <div class="wordmark">
        <div class="wordmark__name">LORVANTI</div>
        <div class="wordmark__country">ITALY</div>
      </div>
    </div>
  </div>
</body>
</html>
```